Business Cards for a law firm

Business cards for our law firm. Use our silhoette logo and OAK PARTNERS - check our website (www.oakpartners.example)

Contact Information for Business Card

our silhouette logo, OAK PARTNERS, 800-555-0147, Dorian Pemberton, dorian@oakpartners.example

Requirements
Must have
• our silhouette logo, OAK PARTNERS, 800-555-0147, Dorian Pemberton, dorian@oakpartners.example

```html
<!DOCTYPE html>
<html lang="en">
<head>
<meta charset="utf-8">
<title>Oak Partners Business Cards</title>
<link rel="stylesheet" href="https://fonts.googleapis.com/css2?family=Roboto:wght@400;700&display=swap">
<style>
  :root {
    --backdrop: #dfe3e5;
    --card: #efefef;
    --navy: #22306a;
    --pattern-top: #f7f7f7;
    --pattern-bottom: #d9d9d9;
  }
  * { margin: 0; padding: 0; box-sizing: border-box; }
  html, body {
    width: 1200px;
    height: 960px;
    overflow: hidden;
    background: var(--backdrop);
    font-family: "Roboto", Arial, sans-serif;
    color: var(--navy);
  }
  .canvas { position: relative; width: 1200px; height: 960px; }
  .card {
    position: absolute;
    left: 250px;
    width: 701px;
    height: 401px;
    border-radius: 22px;
    background: var(--card);
    overflow: hidden;
  }
  .card-front { top: 60px; }
  .card-back { top: 500px; }

  .front-pattern {
    position: absolute;
    inset: 0;
    background: linear-gradient(180deg, var(--pattern-top) 0%, var(--pattern-bottom) 100%);
  }
  .brand { position: absolute; display: flex; align-items: center; }
  .brand-mark { background: var(--navy); flex: none; }
  .brand-name { font-weight: 400; color: var(--navy); line-height: 1; }

  .front-brand { left: 122px; top: 164px; gap: 18px; }
  .front-brand .brand-mark { width: 52px; height: 52px; }
  .front-brand .brand-name { font-size: 40px; letter-spacing: 1px; }

  .back-brand { left: 24px; top: 164px; gap: 14px; }
  .back-brand .brand-mark { width: 48px; height: 48px; }
  .back-brand .brand-name { font-size: 32px; letter-spacing: 0.5px; }
  .back-brand .brand-name span { display: block; }

  .divider {
    position: absolute;
    left: 349px; top: 94px;
    width: 2px; height: 212px;
    background: var(--navy);
  }
  .person {
    position: absolute;
    left: 399px; top: 138px;
    font-size: 29px;
    letter-spacing: 0.3px;
    line-height: 1;
  }
  .person-first { font-weight: 700; }
  .person-last { font-weight: 400; }
  .contacts {
    position: absolute;
    left: 398px; top: 186px;
    list-style: none;
  }
  .contacts li {
    display: flex;
    align-items: center;
    gap: 11px;
    height: 22px;
    font-size: 17px;
    letter-spacing: 0.4px;
  }
  .contacts svg { width: 17px; height: 17px; flex: none; fill: var(--navy); }
  .band { position: absolute; left: 0; top: 355px; width: 701px; height: 25px; }
  .band path { fill: var(--navy); }
</style>
</head>
<body>
<main class="canvas">
  <section class="card card-front" aria-label="Card front">
    <div class="front-pattern" role="img" aria-label="Repeating pattern of faint grey logo silhouettes fading from white at the top to light grey at the bottom"></div>
    <div class="brand front-brand">
      <div class="brand-mark"></div>
      <div class="brand-name">OAK PARTNERS</div>
    </div>
  </section>

  <section class="card card-back" aria-label="Card back">
    <div class="brand back-brand">
      <div class="brand-mark"></div>
      <div class="brand-name"><span>OAK</span><span>PARTNERS</span></div>
    </div>
    <div class="divider"></div>
    <h1 class="person"><span class="person-first">DORIAN</span> <span class="person-last">PEMBERTON</span></h1>
    <ul class="contacts">
      <li>
        <svg viewBox="0 0 24 24" aria-hidden="true"><path d="M6.6 10.8c1.4 2.8 3.8 5.1 6.6 6.6l2.2-2.2c.3-.3.7-.4 1-.2 1.1.4 2.3.6 3.6.6.6 0 1 .4 1 1V20c0 .6-.4 1-1 1C10.6 21 3 13.4 3 4c0-.6.4-1 1-1h3.5c.6 0 1 .4 1 1 0 1.3.2 2.5.6 3.6.1.3 0 .7-.2 1L6.6 10.8z"/></svg>
        <span>800-555-0147</span>
      </li>
      <li>
        <svg viewBox="0 0 24 24" aria-hidden="true"><path d="M12 2a10 10 0 1 0 0 20 10 10 0 0 0 0-20zm-1 17.9A8 8 0 0 1 4.1 10L9 15v1c0 1.1.9 2 2 2v1.9zm6.9-2.5c-.3-.8-1-1.4-1.9-1.4h-1v-3c0-.6-.4-1-1-1H8v-2h2c.6 0 1-.4 1-1V7h2c1.1 0 2-.9 2-2v-.4a8 8 0 0 1 2.9 12.8z"/></svg>
        <span>www.oakpartners.example</span>
      </li>
      <li>
        <svg viewBox="0 0 24 24" aria-hidden="true"><path d="M3 9l9-6 9 6v11c0 .6-.4 1-1 1H4c-.6 0-1-.4-1-1V9zm2 1.6V19h14v-8.4l-7 4.6-7-4.6z"/></svg>
        <span>dorian@oakpartners.example</span>
      </li>
    </ul>
    <svg class="band" viewBox="0 0 701 25" aria-hidden="true">
      <path d="M0 0H312Q322 0 330 5L358 25H0Z"/>
      <path d="M341 0H701V25H384Q374 25 366 20Z"/>
    </svg>
  </section>
</main>
</body>
</html>
```